New Wipes designs - elegant and nice

3 Variants

1. Baby Wipes - Need optons (Blue and Pink colour for Unisex)
2. Mackup Remover - Pink (or you can advice)
3. Abaya Remover - Black or Purple (or you can advice)

Brief for Baby wipes
- Velora Bloom (logo)
- BABY WIPES (nice baby font)
- Eliminates 99% of germs and bacterias, giving healthy and soft skin

Brief for Makeup Remover
- Velora Bloom (logo)
- Makeup Remover
- Special ultra soft formula which gently cleanses and removes makeup and waterproof mascara for the soft skin.

Brief for Baby wipes
- Velora Bloom (logo)
- Abaya Cleaner
- Dummy copy Dummy copy Dummy copy Dummy copy

Mandatory for all wipes
• dermatology tested icon or word
• ph 5.5
• No Alcohol

Target Market(s)

Arab modern women and Asians

Industry/Entity Type

Baby

Requirements
Must have
• Should be feminine and looks elegant, modern, can add premium baby images/ model face where makeup removal effect and abayas... give little tint of arabic pattern.
Nice to have
• you can advice from your side

```html
<!DOCTYPE html>
<html lang="en">
<head>
<meta charset="utf-8">
<title>Velora Bloom Baby Wipes</title>
<link rel="stylesheet" href="https://fonts.googleapis.com/css2?family=Fredoka:wght@500;600&family=Open+Sans:wght@400;700&family=Sofia&display=swap">
<style>
  :root {
    --pink: #e6a4c8;
    --pink-deep: #c77dba;
    --pink-soft: #f6dbe9;
    --sky: #8fcaef;
    --sky-soft: #d6ecfa;
    --blue-text: #3d8fd4;
    --red: #e3394b;
    --crimson: #b3163d;
    --white: #ffffff;
    --photo-light: #f7e6de;
    --photo-mid: #eac9bf;
  }
  html, body {
    margin: 0;
    padding: 0;
    overflow: hidden;
    background: #ffffff;
  }
  .label {
    position: relative;
    width: 1200px;
    height: 686px;
    overflow: hidden;
    background:
      radial-gradient(circle at 270px 300px, #fdf3f6 0 210px, rgba(253,243,246,0) 300px),
      linear-gradient(135deg, #f3c6dd 0%, var(--pink) 45%, var(--pink-deep) 100%);
    font-family: "Open Sans", sans-serif;
  }
  .swirl {
    position: absolute;
    left: -60px;
    top: -60px;
    width: 660px;
    height: 660px;
  }
  .baby-photo {
    position: absolute;
    left: 640px;
    top: 0;
    width: 560px;
    height: 686px;
    background:
      radial-gradient(ellipse 230px 280px at 320px 380px, var(--photo-mid) 0%, var(--photo-light) 55%, transparent 80%),
      radial-gradient(ellipse 330px 420px at 320px 330px, #ffffff 0%, #f4eef0 55%, transparent 85%);
  }
  .brand-name {
    position: absolute;
    left: 110px;
    top: 118px;
    width: 340px;
    text-align: center;
    margin: 0;
    font-family: "Fredoka", sans-serif;
    font-weight: 600;
    font-size: 62px;
    line-height: 64px;
    color: var(--crimson);
  }
  .product-title {
    position: absolute;
    left: 40px;
    top: 318px;
    width: 610px;
    text-align: center;
    margin: 0;
    font-family: "Fredoka", sans-serif;
    font-weight: 600;
    font-size: 104px;
    line-height: 1;
    color: var(--blue-text);
  }
  .claims {
    position: absolute;
    left: 20px;
    top: 448px;
    width: 640px;
    text-align: center;
    margin: 0;
    font-size: 29px;
    line-height: 40px;
    color: var(--red);
  }
  .alcohol-free {
    position: absolute;
    left: 70px;
    top: 536px;
    width: 520px;
    text-align: center;
    margin: 0;
    font-family: "Sofia", cursive;
    font-size: 48px;
    line-height: 70px;
    color: var(--blue-text);
  }
  .ph-badge {
    position: absolute;
    left: 640px;
    top: 390px;
    width: 124px;
    height: 124px;
    border-radius: 50%;
    background: var(--red);
    box-shadow: inset 0 0 0 5px var(--white), 0 0 0 3px var(--red);
    color: var(--white);
    font-family: "Sofia", cursive;
    text-align: center;
  }
  .ph-badge .ph-label { display: block; font-size: 46px; line-height: 46px; margin-top: 14px; }
  .ph-badge .ph-value { display: block; font-size: 36px; line-height: 40px; }
  .tested-badge {
    position: absolute;
    left: 550px;
    top: 505px;
    width: 126px;
    height: 126px;
  }
  .tested-badge text {
    font-family: "Open Sans", sans-serif;
    font-weight: 700;
    font-size: 11.5px;
    letter-spacing: 0.6px;
    fill: var(--white);
  }
  .peel {
    position: absolute;
    right: 0;
    top: 0;
    width: 260px;
    height: 230px;
  }
  .count {
    position: absolute;
    right: 18px;
    top: 18px;
    width: 110px;
    text-align: center;
    color: var(--white);
  }
  .count .count-number { display: block; font-family: "Sofia", cursive; font-size: 78px; line-height: 86px; }
  .count .count-unit { display: block; font-size: 26px; line-height: 28px; }
</style>
</head>
<body>
<main class="label">
  <svg class="swirl" viewBox="0 0 660 660" aria-hidden="true">
    <defs>
      <linearGradient id="swirlBlue" x1="0" y1="0" x2="1" y2="1">
        <stop offset="0" stop-color="#d7ecfb"/>
        <stop offset="1" stop-color="#8fcaef"/>
      </linearGradient>
    </defs>
    <circle cx="330" cy="340" r="270" fill="none" stroke="url(#swirlBlue)" stroke-width="60" opacity="0.75"/>
    <circle cx="330" cy="340" r="225" fill="none" stroke="#e8f4fc" stroke-width="26" opacity="0.6"/>
  </svg>

  <div class="baby-photo" role="img" aria-label="Smiling baby wrapped in a soft white towel"></div>

  <h1 class="brand-name">Velora<br>Bloom</h1>
  <h2 class="product-title">Baby Wipes</h2>
  <p class="claims">Eliminates 99% of germs and bacterias<br>Giving healthy and soft skin</p>
  <p class="alcohol-free">Alcohol Free</p>

  <div class="ph-badge"><span class="ph-label">ph</span><span class="ph-value">5.5</span></div>

  <svg class="tested-badge" viewBox="0 0 126 126" role="img" aria-label="Dermatologically tested">
    <defs>
      <path id="arcTop" d="M22 63 A41 41 0 0 1 104 63"/>
      <path id="arcBottom" d="M26 63 A37 37 0 0 0 100 63"/>
    </defs>
    <circle cx="63" cy="63" r="61" fill="#e3394b"/>
    <circle cx="63" cy="63" r="56" fill="none" stroke="#ffffff" stroke-width="3"/>
    <text><textPath href="#arcTop" startOffset="50%" text-anchor="middle">DERMATOLOGICALLY</textPath></text>
    <text dy="9"><textPath href="#arcBottom" startOffset="50%" text-anchor="middle">TESTED</textPath></text>
    <circle cx="63" cy="63" r="27" fill="#ffffff"/>
    <path d="M63 42 C55 52 49 58 49 66 A14 14 0 0 0 77 66 C77 58 71 52 63 42 Z" fill="#e3394b"/>
    <path d="M58 56 h3 v-3 h4 v3 h3 v4 h-3 v3 h-4 v-3 h-3 Z" fill="#ffffff"/>
    <path d="M55 68 l5 5 l10 -10" fill="none" stroke="#ffffff" stroke-width="3" stroke-linecap="round" stroke-linejoin="round"/>
  </svg>

  <svg class="peel" viewBox="0 0 260 230" aria-hidden="true">
    <defs>
      <linearGradient id="peelFold" x1="0" y1="0" x2="1" y2="1">
        <stop offset="0" stop-color="#ffffff"/>
        <stop offset="0.6" stop-color="#ececf0"/>
        <stop offset="1" stop-color="#c9c9d1"/>
      </linearGradient>
    </defs>
    <path d="M0 0 H260 V230 Z" fill="#c77dba"/>
    <path d="M0 0 C40 30 70 120 60 150 C120 150 200 180 260 230 C180 160 90 80 0 0 Z" fill="url(#peelFold)"/>
  </svg>

  <div class="count"><span class="count-number">72</span><span class="count-unit">wipes</span></div>
</main>
</body>
</html>
```